Hello my name is Colin, I am Starting a business called Lumen Wellness and fitness and am in need of a memorable business card.
It is a personal training studio. I have added the logo that i would like to be on the left center om my business card. i would like room left up the top for a heading sentence such as. "Is your body shocking for all the wrong reasons". there must be room left on the right of the logo below the main heading for 3 sub headings.
then under those 3 headings and logo room for another larger heading eg. "give me a call and learn how to eat chocolate, drink bear and have great sex". in what room is left i would like to be used for my contact details, use I'm Colin Ferrante your fitness expert on the left then on the right Phone, Email and website space in at least 12 Point. Very specific i know :) now onto the back, for the back i would like an eye catching graphic and room for one main headline and 3 bullet points centered just write anything i will choose what to put in them when i pick a winner. Thank you very much for sticking through all of that :) i appreciate you taking the time to read it and hopefully undergo designing me a business card.
I can't wait to see the designs!

Target Market(s)

slightly more towards females although it would probably be best if it was targeted towards both sexes

Industry/Entity Type

Training

Requirements
Nice to have
• I would love to see if anyone could come up with a design that would really make my card stand out and be memorable.
Should not have
• tacky fitness photos of abs and muscles etc.

```html
<!DOCTYPE html>
<html lang="en">
<head>
<meta charset="utf-8">
<title>Lumen Wellness and fitness – Business Card</title>
<link href="https://fonts.googleapis.com/css2?family=Questrial&display=swap" rel="stylesheet">
<style>
  :root {
    --page: #ffffff;
    --navy: #1c3d7c;
    --navy-deep: #163467;
    --sky: #a9bcdb;
    --sub-faint: #8fa6cf;
    --body-light: #d6e0f1;
    --white: #ffffff;
    --photo-warm: #f6e7c8;
    --photo-mid: #d9b58a;
    --photo-road: #5e5a57;
    --bullet-text: #1f3f7a;
  }
  * { box-sizing: border-box; margin: 0; padding: 0; }
  html, body { width: 1200px; height: 848px; overflow: hidden; background: var(--page); }
  body { position: relative; font-family: "Questrial", "Century Gothic", sans-serif; }

  .card {
    position: absolute;
    top: 280px;
    width: 393px;
    height: 217px;
    overflow: hidden;
    box-shadow: 4px 5px 7px rgba(0,0,0,0.35);
  }
  .card--front {
    left: 165px;
    background: linear-gradient(180deg, var(--navy-deep) 0%, var(--navy) 25%, #5a78ad 65%, var(--sky) 88%);
  }
  .card--back { left: 609px; }

  .headline {
    position: absolute;
    color: var(--white);
    font-size: 24px;
    font-weight: 400;
    line-height: 27px;
    letter-spacing: -0.2px;
  }
  .card--front .headline { right: 12px; top: 8px; text-align: right; width: 360px; }

  .brand {
    position: absolute;
    left: 0; top: 62px;
    width: 188px; height: 72px;
    background: var(--white);
    border-radius: 0 8px 8px 0;
    display: flex; align-items: center; gap: 8px;
    padding-left: 14px;
  }
  .brand__dot { width: 14px; height: 14px; border-radius: 50%; background: var(--navy); flex: none; }
  .brand__name { color: var(--navy); font-size: 17px; line-height: 19px; }

  .subheads {
    position: absolute;
    left: 229px; top: 76px;
    list-style: none;
    color: var(--sub-faint);
    font-size: 11px;
    line-height: 20px;
  }
  .subheads li::before { content: "•"; margin-right: 8px; }

  .pitch {
    position: absolute;
    left: 14px; top: 148px;
    width: 372px;
    color: var(--body-light);
    font-size: 12px;
    line-height: 15px;
  }
  .pitch strong { color: var(--navy); font-weight: 400; }

  .contact-band {
    position: absolute;
    left: 0; bottom: 0;
    width: 100%; height: 28px;
    background: var(--white);
    color: var(--navy);
    font-size: 11px;
    white-space: nowrap;
    display: flex; align-items: center;
    padding-left: 14px;
  }

  .back-photo {
    position: absolute; inset: 0;
    background:
      linear-gradient(180deg, var(--photo-warm) 0%, #fbf2de 40%, var(--photo-mid) 62%, var(--photo-road) 100%);
  }
  .card--back .headline {
    left: 14px; top: 6px; width: 330px;
    text-shadow: 1px 1px 2px rgba(30,40,70,0.8);
  }
  .bullets {
    position: absolute;
    left: 233px; top: 56px;
    list-style: none;
    color: var(--bullet-text);
    font-size: 11px;
    line-height: 18px;
  }
  .bullets li::before { content: "•"; margin-right: 8px; }
</style>
</head>
<body>
  <section class="card card--front" aria-label="Business card front">
    <h1 class="headline">Is your body shocking for all the wrong reasons?</h1>
    <div class="brand">
      <span class="brand__dot"></span>
      <span class="brand__name">Lumen Wellness<br>and fitness</span>
    </div>
    <ul class="subheads">
      <li>Sub Heading 1</li>
      <li>Sub Heading 2</li>
      <li>Sub Heading 3</li>
    </ul>
    <p class="pitch">Give me a call and learn how to eat chocolate, drink beer and have great sex! I'm <strong>Colin Ferrante</strong> your fitness expert.</p>
    <div class="contact-band">Tel: 0400 555 218 | Email: colin@lumenfit.com.au | Website: www.lumenfit.com</div>
  </section>

  <section class="card card--back" aria-label="Business card back">
    <div class="back-photo" role="img" aria-label="Photo of a runner's legs in pink running shoes on a road at sunrise"></div>
    <h2 class="headline">Is your body shocking for all the wrong reasons?</h2>
    <ul class="bullets">
      <li>Sub Heading 1</li>
      <li>Sub Heading 2</li>
      <li>Sub Heading 3</li>
    </ul>
  </section>
</body>
</html>
```